Re-style home page - eye-catching and unique design for social commerce website

We need a new concept design for BrinoKet's home page.
We don't want to make huge changes but creating a more professional and eye-catching style.

We need to look very serious like a professional services company and in the same time to look like a social network for e-commerce.

Our logo is very captive and you can use to creating something of harmonious.

This is a re-style and I'm excepted to see unique and fresh design like Glimmora.

Target Market(s)

e-commerce and social

Industry/Entity Type

Social

Number of Pages Required

1 page

Font styles to use
Serif
Sans Serif

Requirements
Must have
• An eye-catching result.
• Search bar with logo and Login How it works and business
• The slogan with login and signup.
• Footer links.
Nice to have
• I would like to open the home page and see only two clear ways:
• -Consumer
• --Search
• --The slogan
• --Login and Signup
• --How it works
• -Business
• --Go to Business area
• Background: City, Shopping.
Should not have
• Scrollbar style!

```html
<!DOCTYPE html>
<html lang="en">
<head>
<meta charset="utf-8">
<title>BrinoKet — Shop directly from your profile</title>
<link rel="stylesheet" href="https://fonts.googleapis.com/css2?family=Montserrat:wght@400;500;600;700&display=swap">
<style>
  :root {
    --night: #0d1030;
    --night-deep: #080a22;
    --header-bg: rgba(8, 10, 34, 0.92);
    --green: #5ea51d;
    --white: #ffffff;
    --muted: rgba(255, 255, 255, 0.6);
    --tag-bg: rgba(150, 40, 50, 0.45);
    --social-blue: #4a5f98;
    --placeholder: #9a9a9a;
  }
  * { margin: 0; padding: 0; box-sizing: border-box; }
  html, body {
    width: 1200px;
    height: 675px;
    overflow: hidden;
    background: var(--night);
    font-family: "Montserrat", Arial, sans-serif;
    color: var(--white);
  }
  .page {
    position: relative;
    width: 1200px;
    height: 675px;
    overflow: hidden;
  }
  .city-backdrop {
    position: absolute;
    inset: 0;
    background:
      radial-gradient(ellipse at 22% 40%, rgba(150, 110, 90, 0.55), transparent 45%),
      radial-gradient(ellipse at 85% 30%, rgba(120, 100, 120, 0.45), transparent 40%),
      linear-gradient(180deg, #3b3550 0%, #2a2a4a 45%, #1c1d40 75%, #12143a 100%);
  }
  .site-header {
    position: absolute;
    top: 0; left: 0;
    width: 100%;
    height: 59px;
    background: var(--header-bg);
  }
  .brand {
    position: absolute;
    left: 88px;
    top: 12px;
    display: flex;
    align-items: center;
    gap: 8px;
    font-size: 30px;
    font-weight: 600;
    letter-spacing: -0.5px;
    line-height: 34px;
  }
  .brand-mark {
    width: 18px; height: 18px;
    background: var(--white);
    border-radius: 50%;
  }
  .search-form {
    position: absolute;
    left: 350px;
    top: 11px;
    display: flex;
    height: 34px;
  }
  .search-input {
    width: 431px;
    height: 34px;
    background: var(--white);
    border-radius: 4px 0 0 4px;
    color: var(--placeholder);
    font-size: 12px;
    line-height: 34px;
    padding-left: 14px;
  }
  .search-button {
    width: 69px;
    height: 34px;
    background: var(--green);
    border-radius: 0 4px 4px 0;
    font-size: 13px;
    font-weight: 600;
    line-height: 34px;
    text-align: center;
  }
  .header-nav {
    position: absolute;
    top: 21px;
    left: 970px;
    display: flex;
    gap: 25px;
    font-size: 13px;
    font-weight: 500;
  }
  .hero-card {
    position: absolute;
    left: 350px;
    top: 112px;
    width: 500px;
    height: 388px;
    border-radius: 14px;
    overflow: hidden;
  }
  .hero-photo {
    position: absolute;
    inset: 0;
    background:
      radial-gradient(ellipse at 80% 65%, rgba(120, 70, 50, 0.9), transparent 38%),
      radial-gradient(ellipse at 78% 88%, rgba(220, 70, 90, 0.85), transparent 30%),
      linear-gradient(120deg, #c98872 0%, #e0856a 45%, #e86a5e 75%, #d96a6a 100%);
  }
  .hero-content {
    position: relative;
    text-align: center;
  }
  .hero-title {
    margin-top: 34px;
    font-size: 23.5px;
    font-weight: 700;
    line-height: 28px;
  }
  .hero-slogan {
    margin-top: 2px;
    font-size: 14px;
    font-weight: 400;
  }
  .category-list {
    position: absolute;
    left: 64px;
    top: 108px;
    display: flex;
    flex-direction: column;
    gap: 6px;
  }
  .category-row { display: flex; gap: 6px; }
  .category-tag {
    height: 19.5px;
    padding: 0 5px;
    background: var(--tag-bg);
    border-radius: 2px;
    font-size: 11px;
    line-height: 19.5px;
    white-space: nowrap;
  }
  .social-signin {
    position: absolute;
    left: 167px;
    top: 270px;
    width: 163px;
    height: 36px;
    background: var(--social-blue);
    border-radius: 3px;
    display: flex;
    align-items: center;
    gap: 14px;
    padding-left: 12px;
    font-size: 10px;
    font-weight: 600;
  }
  .social-signin-mark {
    width: 8px; height: 8px;
    background: var(--white);
  }
  .signup-button {
    position: absolute;
    left: 167px;
    top: 323px;
    width: 163px;
    height: 35px;
    border: 2px solid var(--white);
    border-radius: 4px;
    font-size: 11px;
    font-weight: 600;
    line-height: 31px;
    text-align: center;
  }
  .business-button {
    position: absolute;
    left: 518px;
    top: 523px;
    width: 163px;
    height: 36px;
    background: var(--green);
    border-radius: 3px;
    display: flex;
    align-items: center;
    justify-content: center;
    gap: 10px;
    font-size: 10.5px;
    font-weight: 600;
  }
  .site-footer {
    position: absolute;
    top: 612px;
    left: 0;
    width: 100%;
    text-align: center;
  }
  .footer-links {
    display: flex;
    justify-content: center;
    gap: 26px;
    font-size: 10px;
    color: var(--muted);
  }
  .footer-links .is-current { color: var(--white); }
  .copyright {
    margin-top: 16px;
    font-size: 9.5px;
    color: var(--muted);
  }
</style>
</head>
<body>
<div class="page">
  <div class="city-backdrop" role="img" aria-label="Blurred photo of a busy city shopping street with pedestrians and storefronts"></div>

  <header class="site-header">
    <div class="brand"><span>BrinoKet</span><span class="brand-mark"></span></div>
    <div class="search-form">
      <div class="search-input">Search keywords</div>
      <div class="search-button">Search</div>
    </div>
    <nav class="header-nav">
      <span>How It Works</span>
      <span>Login</span>
    </nav>
  </header>

  <section class="hero-card">
    <div class="hero-photo" role="img" aria-label="Warm close-up photo of chocolate cupcakes in pink paper cases"></div>
    <div class="hero-content">
      <h1 class="hero-title">Shop directly from your profile</h1>
      <p class="hero-slogan">Save your time. Live better.</p>
    </div>
    <div class="category-list">
      <div class="category-row">
        <span class="category-tag">Active life</span>
        <span class="category-tag">Arts &amp; Entertainment</span>
        <span class="category-tag">Automotive</span>
        <span class="category-tag">Beauty &amp; Spas</span>
      </div>
      <div class="category-row">
        <span class="category-tag">Education</span>
        <span class="category-tag">Event Planning &amp; Services</span>
        <span class="category-tag">Financial Services</span>
        <span class="category-tag">Food</span>
      </div>
      <div class="category-row">
        <span class="category-tag">Health &amp; Medical</span>
        <span class="category-tag">Home Services</span>
        <span class="category-tag">Hotels</span>
        <span class="category-tag">Local Services</span>
      </div>
      <div class="category-row">
        <span class="category-tag">Mass Media</span>
        <span class="category-tag">Nightlife</span>
        <span class="category-tag">Pets</span>
        <span class="category-tag">Professional Services</span>
      </div>
      <div class="category-row">
        <span class="category-tag">Public Services &amp; Government</span>
        <span class="category-tag">Real Estate</span>
        <span class="category-tag">Restaurants</span>
      </div>
      <div class="category-row">
        <span class="category-tag">Shopping</span>
      </div>
    </div>
    <div class="social-signin"><span class="social-signin-mark"></span><span>Sign in with Connectly</span></div>
    <div class="signup-button">Sign Up</div>
  </section>

  <div class="business-button">
    <span>Go to Business Area</span>
    <svg width="26" height="8" viewBox="0 0 26 8" aria-hidden="true">
      <line x1="0" y1="4" x2="25" y2="4" stroke="#fff" stroke-width="1"/>
      <polyline points="21,1 25,4 21,7" fill="none" stroke="#fff" stroke-width="1"/>
    </svg>
  </div>

  <footer class="site-footer">
    <nav class="footer-links">
      <span class="is-current">About Us</span>
      <span>Blog</span>
      <span>Business</span>
      <span>Jobs</span>
      <span>Privacy</span>
      <span>FAQ</span>
      <span>Contacts</span>
    </nav>
    <p class="copyright">© 2015 BrinoKet. All right reserved.</p>
  </footer>
</div>
</body>
</html>
```